New Business Card Design for Manufacturing

We are an engineering/manufacturing company that offers Advanced machining/assembly/engineering services, as well as innovative products for the heavy duty engine cooling markets.

We are looking to get a new business card designed that is clean and modern looking, but still fits the wide range of technical/skilled work we do.

- We hope to use this design as the base for other design work in new Presentations, web, and print work.

Industry/Entity Type

Engineering

Contact Information for Business Card

Our preferred color of blue is (RGB) 22/71/159 but can vary slightly from that color. Our content will be our Logo and full company name (Vantrell Forge Works, Inc.), company address, name, job title, phone number with extension, cell number, fax number, website, and email address on the cards.
We'd like the full company name next to the logo, but we are open to other interpretations of that layout.
Preferably, we would like the back side to be clean with just our logo, and the front to contain all of the contact information.

Colors
2f74b4
0355a3
85abd2

Requirements
Must have
• - Logo, company name, needed content - We are open to interpretation beyond that.
• - Standard size business card.
• - Horizontal orientation.
• - Enough space for lengthy names / job titles (for example, a job title could read "Directory of Human Resources" or "V.P. of Governmental Affairs"). We need this to look clean, whether the title be short (CEO) or long (as described above).

```html
<!DOCTYPE html>
<html lang="en">
<head>
<meta charset="utf-8">
<title>Vantrell Forge Works – Business Card</title>
<link href="https://fonts.googleapis.com/css2?family=Roboto:wght@400;500;700;900&family=Roboto+Condensed:wght@500;700&display=swap" rel="stylesheet">
<style>
  :root {
    --brand-blue: #0e50a0;
    --ink: #1d1d1d;
    --muted: #555a60;
    --card-white: #f4f4f4;
    --backdrop: #2b2b2b;
    --rule: #b9bcc0;
    --tagline-grey: #80858a;
  }
  * { margin: 0; padding: 0; box-sizing: border-box; }
  html, body { width: 1200px; height: 960px; overflow: hidden; }
  body { background: var(--backdrop); font-family: "Roboto", Arial, sans-serif; position: relative; }

  .card { position: absolute; width: 600px; height: 343px; overflow: hidden; }
  .card--front { left: 314px; top: 113px; background: var(--card-white); }
  .card--back { left: 311px; top: 472px; background: var(--brand-blue); }

  .front-wedges { position: absolute; inset: 0; }

  .brand-front { position: absolute; left: 66px; top: 128px; white-space: nowrap; }
  .brand-front__name {
    font-weight: 900; font-size: 44px; line-height: 1; color: var(--brand-blue);
    letter-spacing: -0.5px; text-transform: uppercase;
  }
  .brand-front__tagline {
    margin-top: 8px; font-weight: 700; font-size: 14px;
    color: var(--tagline-grey); text-transform: uppercase; letter-spacing: 0.2px;
  }

  .divider { position: absolute; left: 315px; top: 88px; width: 1px; height: 170px; background: var(--rule); }

  .contact { position: absolute; left: 346px; top: 86px; white-space: nowrap; }
  .contact__name {
    font-family: "Roboto Condensed", Arial, sans-serif; font-weight: 700;
    font-size: 23px; color: var(--brand-blue); line-height: 1; letter-spacing: 0.2px;
  }
  .contact__title { margin-top: 4px; font-size: 14px; color: var(--ink); letter-spacing: 0.2px; }
  .contact__address { margin-top: 8px; font-size: 14px; line-height: 18px; color: var(--muted); letter-spacing: 0.2px; }
  .contact__list { list-style: none; margin-top: 10px; }
  .contact__item { display: flex; align-items: center; font-size: 14px; line-height: 19.5px; color: var(--muted); letter-spacing: 0.2px; }
  .contact__icon { width: 12px; height: 12px; margin-right: 10px; fill: var(--brand-blue); flex: none; }

  .brand-back {
    position: absolute; left: 107px; top: 132px;
    display: flex; align-items: flex-start; color: #fff; white-space: nowrap;
  }
  .brand-back__mark { flex: none; }
  .brand-back__name { font-weight: 900; font-size: 44px; line-height: 1; letter-spacing: -0.5px; text-transform: uppercase; }
  .brand-back__tagline { margin-top: 8px; font-weight: 700; font-size: 14px; text-transform: uppercase; letter-spacing: 0.2px; }
  .brand-back__company {
    flex: none; margin-left: 20px; margin-top: 0;
    font-weight: 900; font-size: 16px; line-height: 20px; text-transform: uppercase;
  }
</style>
</head>
<body>

<section class="card card--front" aria-label="Business card front">
  <svg class="front-wedges" width="600" height="343" viewBox="0 0 600 343" aria-hidden="true">
    <polygon points="0,0 62,0 2,343 0,343" fill="var(--brand-blue)"/>
    <polygon points="600,0 599,0 537,343 600,343" fill="var(--brand-blue)"/>
  </svg>

  <div class="brand-front">
    <div class="brand-front__name">Vantrell</div>
    <div class="brand-front__tagline">Built to Run Cool</div>
  </div>

  <div class="divider"></div>

  <div class="contact">
    <div class="contact__name">DORIAN HALVERS</div>
    <div class="contact__title">V.P. of Governmental Affairs</div>
    <div class="contact__address">4120 Larkspur Road<br>Anchorage, Alaska 99512</div>
    <ul class="contact__list">
      <li class="contact__item">
        <svg class="contact__icon" viewBox="0 0 24 24" aria-hidden="true"><path d="M6.6 10.8a15.2 15.2 0 0 0 6.6 6.6l2.2-2.2c.3-.3.7-.4 1-.2 1.1.4 2.3.6 3.6.6.6 0 1 .4 1 1V20c0 .6-.4 1-1 1A17 17 0 0 1 3 4c0-.6.4-1 1-1h3.5c.6 0 1 .4 1 1 0 1.3.2 2.5.6 3.6.1.3 0 .7-.2 1z"/></svg>
        907 555 0142
      </li>
      <li class="contact__item">
        <svg class="contact__icon" viewBox="0 0 24 24" aria-hidden="true"><path d="M7 1h10a2 2 0 0 1 2 2v18a2 2 0 0 1-2 2H7a2 2 0 0 1-2-2V3a2 2 0 0 1 2-2zm0 3v14h10V4zm5 15.5a1 1 0 1 0 0 2 1 1 0 0 0 0-2z"/></svg>
        907 555 0187
      </li>
      <li class="contact__item">
        <svg class="contact__icon" viewBox="0 0 24 24" aria-hidden="true"><path d="M2 5h20v14H2zm2 2v.5l8 5 8-5V7z"/></svg>
        dorian@vantrell.com
      </li>
      <li class="contact__item">
        <svg class="contact__icon" viewBox="0 0 24 24" aria-hidden="true"><circle cx="12" cy="12" r="10"/><path d="M2 12h20M12 2c3 3 3 17 0 20M12 2c-3 3-3 17 0 20" stroke="#fff" stroke-width="1.4" fill="none"/></svg>
        www.vantrell.com
      </li>
    </ul>
  </div>
</section>

<section class="card card--back" aria-label="Business card back">
  <div class="brand-back">
    <div class="brand-back__mark">
      <div class="brand-back__name">Vantrell</div>
      <div class="brand-back__tagline">Built to Run Cool</div>
    </div>
    <div class="brand-back__company">Vantrell<br>Forge Works<br>Inc.</div>
  </div>
</section>

</body>
</html>
```